Fenwick Grading LTD - website for irrigation & Landscape Lighting & Buried service wire

Looking for a website to help promote my business with Irrigation (installation, service, etc) and buried service wire/drainage solutions.

Commercial/Residential

Landscape lighting.

I’ll get photos in the trucks and trailers to upload as well maybe the machine as well.

Target Market(s)

Homeowners who want green grass and beautiful gardens. Beautiful landscape lighting

Industry/Entity Type

Irrigation systems and landscape lighting and buried service wire to homes and offering Drainage soltions.

Coding

Coded - Design and coding required

Number of Pages Required

4 page

Colors
F0912C
F2A743
F7CA91
FBE8D2
FDF5EE

Requirements
Must have
• was hoping to link up my email on fenwickgrading@mailbox-example.net with the website if possible.
Nice to have
• Page for Irrigation, page for landscape lighting, page buried service wire & drainage soltions.

```html
<!DOCTYPE html>
<html lang="en">
<head>
<meta charset="utf-8">
<title>Fenwick Grading LTD</title>
<link href="https://fonts.googleapis.com/css2?family=Montserrat:wght@400;500;600;700&display=swap" rel="stylesheet">
<style>
:root{
  --orange:#F0912C;
  --orange-soft:#F2A743;
  --peach:#F7CA91;
  --sand:#FBE8D2;
  --cream:#FDF5EE;
  --ink:#111111;
  --body:#5a5a5a;
  --footer:#1c1b1a;
  --white:#ffffff;
}
*{margin:0;padding:0;box-sizing:border-box}
html,body{width:1200px;height:2928px;overflow:hidden}
body{position:relative;font-family:'Montserrat',sans-serif;color:var(--ink);background:var(--white)}
.abs{position:absolute}
a{color:inherit;text-decoration:none}

/* header */
.site-header{position:absolute;left:0;top:0;width:1200px;height:70px;background:var(--white);z-index:3}
.brand{position:absolute;left:141px;top:14px;display:flex;align-items:center;gap:8px}
.brand-dot{width:14px;height:14px;border-radius:50%;background:var(--orange)}
.brand-name{color:var(--orange);font-weight:600;font-size:15px;line-height:18px;letter-spacing:.5px}
.main-nav{position:absolute;top:26px;left:0;font-size:14px;font-weight:500}
.main-nav a{position:absolute;white-space:nowrap}
.main-nav a.active{color:var(--orange);border-bottom:1.5px solid var(--orange);padding-bottom:2px}
.btn{display:inline-block;background:var(--orange);color:var(--white);font-size:12px;font-weight:600;letter-spacing:1px;border-radius:20px;text-transform:uppercase;text-align:center}
.btn-contact{position:absolute;left:940px;top:18px;width:118px;height:34px;line-height:34px;background:var(--white);color:var(--orange);z-index:4}

/* hero */
.hero{position:absolute;left:0;top:0;width:1200px;height:558px;background:var(--cream)}
.hero-art{position:absolute;left:0;top:0;z-index:2}
.hero-title{position:absolute;left:141px;top:206px;font-size:33px;font-weight:500;line-height:48px;z-index:3}
.accent{color:var(--orange)}
.lead{position:absolute;border-left:2px solid var(--orange);padding-left:11px;font-size:13.5px;font-weight:500;line-height:23px;color:var(--ink)}
.hero .lead{left:141px;top:363px;width:440px;z-index:3}
.btn-quote{position:absolute;left:141px;top:431px;width:160px;height:35px;line-height:35px;z-index:3}

/* services */
.service-art{position:absolute}
.service-title{position:absolute;font-size:26px;font-weight:500}
.service-text{position:absolute;font-size:13.5px;line-height:22.7px;color:var(--body)}
.btn-more{position:absolute;width:122px;height:35px;line-height:35px}

/* testimonials */
.section-title{position:absolute;left:0;width:1200px;text-align:center;font-size:26px;font-weight:600}
.section-sub{position:absolute;left:0;width:1200px;text-align:center;font-size:13.5px;font-weight:500}
.quote-text{position:absolute;left:141px;top:2259px;width:480px;font-size:13.5px;line-height:22.7px;color:var(--ink)}
.quote-name{position:absolute;left:141px;top:2387px;font-size:16px;font-weight:600;color:var(--orange)}
.slider-arrows{position:absolute;left:141px;top:2462px}
.portrait{position:absolute}

/* footer */
.site-footer{position:absolute;left:0;top:2613px;width:1200px;height:315px;background:linear-gradient(180deg,#23221f,#151413);color:var(--white)}
.footer-brand{position:absolute;left:141px;top:78px;display:flex;align-items:center;gap:12px}
.footer-brand .brand-dot{width:22px;height:22px}
.footer-brand .brand-name{font-size:30px;line-height:36px;font-weight:600;letter-spacing:1px}
.footer-col{position:absolute;top:56px}
.footer-col h3{color:var(--orange);font-size:16px;font-weight:600;margin-bottom:12px}
.footer-col li{list-style:none;font-size:13.5px;line-height:27.5px}
.contact-item{display:flex;gap:12px;font-size:13.5px;line-height:21px;margin-bottom:10px}
.contact-item svg{flex:none;margin-top:2px}
.footer-rule{position:absolute;left:141px;top:256px;width:918px;height:1px;background:rgba(255,255,255,.25)}
.copyright{position:absolute;left:141px;top:277px;font-size:13px}
.socials{position:absolute;left:925px;top:272px;display:flex;gap:11px}
.socials span{width:25px;height:25px;border-radius:50%;background:var(--orange)}
</style>
</head>
<body>

<header class="site-header">
  <a class="brand" href="#"><span class="brand-dot"></span><span class="brand-name">FENWICK<br>GRADING LTD</span></a>
  <nav class="main-nav">
    <a class="active" href="#" style="left:385px">Home</a>
    <a href="#" style="left:452px">Irrigation</a>
    <a href="#" style="left:540px">Landscape Lighting</a>
    <a href="#" style="left:694px">Fiber Optic Installation</a>
  </nav>
</header>
<a class="btn btn-contact" href="#">Contact Us</a>

<section class="hero">
  <svg class="hero-art" width="1200" height="558" viewBox="0 0 1200 558">
    <defs>
      <linearGradient id="heroFill" x1="0" y1="0" x2="0" y2="1">
        <stop offset="0" stop-color="#9fb2c8"/>
        <stop offset=".45" stop-color="#c9c39a"/>
        <stop offset=".7" stop-color="#6e8f2c"/>
        <stop offset="1" stop-color="#3c5a1a"/>
      </linearGradient>
    </defs>
    <path d="M646 330 C640 395 720 400 830 408 C920 430 930 505 975 545 C1020 570 1120 560 1200 532" fill="none" stroke="var(--orange)" stroke-width="7"/>
    <path role="img" aria-label="Lawn sprinkler spraying water over a green park at sunset" d="M855 0 L1200 0 L1200 526 C1120 552 1010 558 978 536 C935 500 925 428 830 402 C720 392 646 378 648 330 C652 250 742 228 782 168 C822 108 840 40 855 0 Z" fill="url(#heroFill)"/>
  </svg>
  <h1 class="hero-title">Welcome To <span class="accent">Fenwick Grading</span><br>Your One-Stop Solution For<br>Home Improvement</h1>
  <p class="lead">Expertise In Irrigation Systems, Landscape Lighting, And Fiber Optic Installation</p>
  <a class="btn btn-quote" href="#">Get A Free Quote</a>
</section>

<svg width="0" height="0" style="position:absolute">
  <defs>
    <path id="blob" d="M60 330 C0 300 0 220 40 140 C80 60 130 0 200 10 C260 18 340 90 360 160 C380 240 330 290 240 320 C160 345 110 372 60 330 Z"/>
    <linearGradient id="skyFill" x1="0" y1="0" x2="0" y2="1"><stop offset="0" stop-color="#a9bfd6"/><stop offset=".6" stop-color="#b9b4a8"/><stop offset="1" stop-color="#5d6d4c"/></linearGradient>
    <linearGradient id="gardenFill" x1="0" y1="0" x2="0" y2="1"><stop offset="0" stop-color="#3a4a26"/><stop offset=".5" stop-color="#5f8a2e"/><stop offset="1" stop-color="#4a3a22"/></linearGradient>
    <linearGradient id="deskFill" x1="0" y1="0" x2="1" y2="1"><stop offset="0" stop-color="#d6d0c6"/><stop offset=".55" stop-color="#7a3f22"/><stop offset="1" stop-color="#262423"/></linearGradient>
  </defs>
</svg>

<!-- Irrigation -->
<svg class="service-art" style="left:150px;top:654px" width="390" height="380" viewBox="0 0 390 380">
  <use href="#blob" fill="url(#skyFill)" role="img" aria-label="Rotating irrigation sprinkler head watering a field"/>
  <use href="#blob" transform="translate(10 -4)" fill="none" stroke="var(--orange)" stroke-width="1.5"/>
</svg>
<h2 class="service-title" style="left:639px;top:697px">Irrigation <span class="accent">Systems</span></h2>
<p class="lead" style="left:639px;top:752px;width:400px">Efficient and Effective Watering Solutions for Your Lawn and Garden</p>
<p class="service-text" style="left:639px;top:811px;width:420px">Our irrigation systems are designed to provide your lawn and garden with the right amount of water, without wasting a single drop. With our expert installation and service, you can rest assured that your plants will receive the nourishment they need to thrive.</p>
<a class="btn btn-more" href="#" style="left:639px;top:949px">Learn More</a>

<!-- Lighting -->
<svg class="service-art" style="left:665px;top:1131px" width="390" height="380" viewBox="0 0 390 380">
  <use href="#blob" fill="url(#gardenFill)" role="img" aria-label="Garden path lit by bollard lights at dusk"/>
  <use href="#blob" transform="translate(10 -4)" fill="none" stroke="var(--orange)" stroke-width="1.5"/>
</svg>
<h2 class="service-title" style="left:141px;top:1174px">Landscape <span class="accent">Lighting</span></h2>
<p class="lead" style="left:141px;top:1229px;width:420px">Enhance Your Outdoor Space with Beautiful and Functional Lighting Solutions</p>
<p class="service-text" style="left:141px;top:1288px;width:410px">Our landscape lighting solutions are designed to enhance the beauty and functionality of your outdoor space. From subtle pathway lighting to dramatic spotlights, we'll work with you to create a lighting plan that meets your needs and complements your landscape.</p>
<a class="btn btn-more" href="#" style="left:141px;top:1426px">Learn More</a>

<!-- Fiber -->
<svg class="service-art" style="left:150px;top:1608px" width="390" height="380" viewBox="0 0 390 380">
  <use href="#blob" fill="url(#deskFill)" role="img" aria-label="Technician testing cables with a multimeter on a desk"/>
  <use href="#blob" transform="translate(10 -4)" fill="none" stroke="var(--orange)" stroke-width="1.5"/>
</svg>
<h2 class="service-title" style="left:639px;top:1674px">Fiber Optic <span class="accent">Installation</span></h2>
<p class="lead" style="left:639px;top:1729px;width:420px">Expert Installation of Fiber Optic Networks for Your Home</p>
<p class="service-text" style="left:639px;top:1765px;width:425px">Our team of experienced professionals will install your fiber optic network with precision and care. We'll work with you to ensure that your home is equipped with the latest technology, providing you with fast and reliable internet, TV, and voice services.</p>
<a class="btn btn-more" href="#" style="left:639px;top:1880px">Learn More</a>

<!-- Testimonials -->
<h2 class="section-title" style="top:2078px">What Our <span class="accent">Customers</span> Say</h2>
<p class="section-sub" style="top:2128px">Hear from Our Satisfied Clients</p>
<p class="quote-text">They maintain around 52 acres for us including several thousand sq ft or beds. Always answer thr phone and very prompt if we ever have an issue. Great guys all the way around! It is a long established fact that a reader will be distracted by the readable content of a page when looking at its layout.</p>
<p class="quote-name">Marcus Delby</p>
<svg class="slider-arrows" width="130" height="20" viewBox="0 0 130 20" fill="none" stroke="var(--ink)" stroke-width="1.5">
  <path d="M2 10 H36 M2 10 L9 4 M2 10 L9 16"/>
  <path d="M92 10 H127 M127 10 L120 4 M127 10 L120 16"/>
</svg>
<svg class="portrait" style="left:708px;top:2185px" width="242" height="346" viewBox="0 0 242 346">
  <rect x="8" y="2" width="230" height="340" rx="115" fill="none" stroke="var(--orange)" stroke-width="1.5"/>
  <rect x="3" y="5" width="230" height="338" rx="115" fill="#b9c1c6" role="img" aria-label="Portrait of the featured customer"/>
</svg>
<svg class="portrait" style="left:945px;top:2137px" width="112" height="112"><circle cx="56" cy="56" r="56" fill="#8a5a4c" role="img" aria-label="Portrait of a customer"/></svg>
<svg class="portrait" style="left:592px;top:2407px" width="80" height="80"><circle cx="40" cy="40" r="40" fill="#5f7a86" role="img" aria-label="Portrait of a customer"/></svg>
<svg class="portrait" style="left:967px;top:2418px" width="70" height="70"><circle cx="35" cy="35" r="35" fill="#5b5450" role="img" aria-label="Portrait of a customer"/></svg>

<footer class="site-footer" role="img" aria-label="Dark backdrop of a lit garden at night">
  <div class="footer-brand"><span class="brand-dot"></span><span class="brand-name">FENWICK<br>GRADING LTD</span></div>
  <div class="footer-col" style="left:459px">
    <h3>Quick Links</h3>
    <ul><li>Home</li><li>Irrigation</li><li>Landscape Lighting</li><li>Fiber Optic Installation</li></ul>
  </div>
  <div class="footer-col" style="left:670px">
    <h3>Useful Links</h3>
    <ul><li>Contact</li><li>Privacy Policy</li><li>Terms of Service</li></ul>
  </div>
  <div class="footer-col" style="left:838px;width:300px">
    <h3>Contact Info</h3>
    <div class="contact-item">
      <svg width="18" height="20" viewBox="0 0 18 20" fill="none" stroke="var(--orange)" stroke-width="2"><path d="M9 19 C4 13 3 10 3 8 a6 6 0 0 1 12 0 c0 2 -1 5 -6 11Z"/><circle cx="9" cy="8" r="2"/></svg>
      <span>Address Line 1, Address<br>Line 2, Address Line 3.</span>
    </div>
    <div class="contact-item">
      <svg width="18" height="14" viewBox="0 0 18 14"><rect x="0" y="0" width="18" height="14" rx="2" fill="var(--orange)"/><path d="M1 2 L9 8 L17 2" fill="none" stroke="var(--footer)" stroke-width="1.5"/></svg>
      <span>fenwickgrading@mailbox-example.net</span>
    </div>
    <div class="contact-item">
      <svg width="18" height="18" viewBox="0 0 18 18"><path d="M3 1 L7 1 L8 5 L6 7 C7 10 8 11 11 12 L13 10 L17 11 L17 15 C17 16 16 17 15 17 C7 17 1 11 1 3 C1 2 2 1 3 1Z" fill="var(--orange)"/></svg>
      <span>123-456-7890</span>
    </div>
  </div>
  <div class="footer-rule"></div>
  <p class="copyright">© 2024 Fenwick Grading. All rights reserved.</p>
  <div class="socials"><span></span><span></span><span></span><span></span></div>
</footer>

</body>
</html>
```